Informational Site for Advanced Chemistry R&D

The company develops oxidation chemistry for air, water, fuel pollution controls. The site has been prototyped at www.velquaresearch.example. Take a look. Now, the task is to design it for eye-catching beauty with use of color, on-page scroll-driven color transition and parallax effects. Should capture the themes: high technology, wow it's beautiful, modern, uncluttered, clean urban environment.

Target Market(s)

China Environmentally Conscious Government and Industry,

Industry/Entity Type

It Company

Number of Pages Required

3 page

Font styles to use
Sans Serif

Requirements
Must have
• Parallax effects, desktop compatible, Rich, Modern, Simple, Graphic
Nice to have
• Mobile Phone Compatible
Should not have
• Flash, or anything that is slow to load or requires high bandwidth

```html
<!DOCTYPE html>
<html lang="en">
<head>
<meta charset="utf-8">
<title>Velqua Research — Advanced Oxidation Science</title>
<link href="https://fonts.googleapis.com/css2?family=Quicksand:wght@400;500;700&family=Open+Sans:wght@400;600&display=swap" rel="stylesheet">
<style>
:root{
  --teal:#1fb3bf;
  --teal-dark:#139aa6;
  --blue:#1c86c6;
  --blue-deep:#1670b8;
  --green:#8dc63f;
  --ink:#3d4a55;
  --muted:#8a949c;
  --white:#ffffff;
  --about-top:#4a90b6;
}
*{margin:0;padding:0;box-sizing:border-box}
html,body{width:1200px;height:4235px;overflow:hidden}
body{position:relative;font-family:"Open Sans",Arial,sans-serif;color:var(--ink);background:var(--white)}
.abs{position:absolute}
.heading{font-family:"Quicksand",Arial,sans-serif;font-weight:500}

/* hero */
.hero{left:0;top:0;width:1200px;height:700px;background:linear-gradient(180deg,#eef1f4 0%,#dfe5ea 55%,#e9edf0 100%)}
.brand{font-family:"Quicksand",Arial,sans-serif;font-weight:700;color:var(--teal);display:flex;align-items:center;gap:12px}
.brand .dot{width:34px;height:34px;border-radius:50%;background:var(--teal)}
.nav{top:60px;left:0;width:1200px;height:90px}
.nav .brand{position:absolute;left:85px;top:14px;font-size:30px}
.nav a{position:absolute;top:8px;font-size:15px;color:#4a555e;text-decoration:none}
.nav .center{position:absolute;left:577px;top:-22px;width:76px;height:76px;border:2px solid var(--teal);border-radius:50%;background:#fff;display:flex;align-items:center;justify-content:center;font-size:14px;color:var(--teal)}
.hero-mark{left:566px;top:270px;width:68px;height:68px;border-radius:50%;border:3px solid #b9c0c5}
.hero-title{left:0;top:352px;width:1200px;text-align:center;font-size:46px;color:var(--teal)}
.hero-sub{left:0;top:404px;width:1200px;text-align:center;font-size:34px;color:var(--teal)}
.scroll-btn{left:578px;top:596px;width:40px;height:40px;border:2px solid var(--teal);border-radius:50%}

/* about */
.about{left:0;top:680px;width:1200px;height:628px;background:linear-gradient(170deg,var(--about-top) 0%,#2f78a6 55%,#2c6f9c 100%)}
.about h2{position:absolute;left:88px;top:148px;font-size:44px;color:#fff}
.about h2 span{color:var(--teal)}
.about .copy{position:absolute;left:88px;top:242px;width:620px;font-size:14px;line-height:24px;color:#eef5fa}
.about .copy p{margin-bottom:22px}
.photo-circle{border-radius:50%;border:8px solid var(--teal)}
.about .big{left:757px;top:110px;width:222px;height:222px;background:linear-gradient(180deg,#6fb3dd,#8a8f8c 70%,#6b6258)}
.about .small{left:907px;top:306px;width:200px;height:200px;background:linear-gradient(180deg,#a36b55,#6b3f33)}

/* solutions */
.section-title{left:0;width:1200px;text-align:center;font-size:42px;color:var(--blue)}
.section-sub{left:0;width:1200px;text-align:center;font-size:14px;color:var(--muted)}
.solution{width:320px;text-align:center}
.icon-ring{margin:0 auto;width:124px;height:124px;border-radius:50%;border:7px solid var(--teal);display:flex;align-items:center;justify-content:center}
.solution h3{font-family:"Quicksand",Arial,sans-serif;font-weight:700;font-size:26px;color:var(--blue);margin-top:30px}
.blurb{font-size:13px;line-height:21px;color:var(--muted);margin-top:12px}
.read-more{font-size:13px;color:var(--green);margin-top:22px}
.read-more::before{content:"";display:block;margin:0 auto 6px;width:12px;height:12px;border-radius:50%;background:var(--green)}

/* advanced oxidation */
.oxidation{left:0;top:2019px;width:1200px;height:598px;background:linear-gradient(110deg,#1ca7ad 0%,#43bfb8 50%,#2db0b4 100%)}
.oxidation .photo{position:absolute;left:85px;top:110px;width:384px;height:384px;background:linear-gradient(160deg,#6b8898,#2c4e6e 60%,#1d3552)}
.oxidation h2{position:absolute;left:518px;top:160px;font-size:40px;color:var(--blue-deep)}
.oxidation h2 span{color:#fff}
.oxidation .copy{position:absolute;left:518px;top:232px;width:610px;font-size:14px;line-height:24px;color:#f1fbfb}
.oxidation ul{list-style:none;margin:14px 0 22px}
.oxidation li{padding-left:22px;position:relative}
.oxidation li::before{content:"";position:absolute;left:2px;top:8px;width:9px;height:9px;background:#fff;transform:rotate(45deg)}

/* products */
.product{width:260px;text-align:center}
.product .disc{margin:0 auto;width:186px;height:186px;border-radius:50%;border:7px solid var(--teal)}
.product h3{font-family:"Quicksand",Arial,sans-serif;font-weight:700;font-size:24px;color:var(--ink);margin-top:28px}
.product .kind{font-size:12px;line-height:17px;color:var(--teal);margin-top:6px}
.product hr{border:0;border-top:1px solid #dde2e5;width:170px;margin:12px auto}

/* contact */
.map{left:0;top:3346px;width:1200px;height:482px;background:linear-gradient(180deg,#cfd1d3,#bfc2c5)}
.card{left:373px;top:3402px;width:450px;height:374px;background:#fff;text-align:center}
.card .brand{justify-content:center;margin-top:34px;font-size:28px}
.card .intro{font-size:13px;line-height:21px;color:var(--muted);margin:26px auto 0;width:370px}
.contact-row{display:flex;align-items:center;gap:14px;width:260px;margin:24px auto 0;text-align:left}
.contact-row .ring{flex:none;width:40px;height:40px;border-radius:50%;border:2px solid var(--teal);display:flex;align-items:center;justify-content:center}
.contact-row b{display:block;font-weight:400;font-size:19px;color:var(--ink)}
.contact-row small{font-size:11px;color:var(--muted)}

/* partners */
.partners{left:0;top:3826px;width:1200px;height:300px;background:linear-gradient(180deg,var(--blue-deep),#1b7ec4)}
.partner{width:240px;text-align:center;color:#fff}
.partner .name{font-family:"Quicksand",Arial,sans-serif;font-weight:700;font-size:24px;height:90px;display:flex;align-items:center;justify-content:center}
.partner .badge{width:86px;height:86px;border-radius:50%;border:3px solid #fff;margin:2px auto}
.partner .cap{font-size:13px;line-height:18px;color:#8fc6ec;margin-top:14px}

/* footer */
.footer{left:0;top:4088px;width:1200px;height:147px;background:#1a7bc1}
.footer .brand{position:absolute;left:128px;top:70px;font-size:24px;color:#fff}
.footer .brand .dot{background:#fff;width:26px;height:26px}
.footer .rule{position:absolute;top:92px;height:1px;background:#5fa6d8}
.social{position:absolute;top:72px;width:40px;height:40px;border-radius:50%;border:2px solid #fff}
.footer .copy{position:absolute;right:60px;top:84px;font-size:12px;color:#d7ebf8}
</style>
</head>
<body>

<!-- Hero -->
<div class="abs hero" role="img" aria-label="Faded city skyline reflected on a river"></div>
<header class="abs nav">
  <div class="brand"><span class="dot"></span>Velqua</div>
  <a style="left:458px">About</a>
  <div class="center">Solutions</div>
  <a style="left:740px">Technology</a>
  <a style="left:910px">Products</a>
  <a style="left:1060px">Contact</a>
</header>
<div class="abs hero-mark"></div>
<h1 class="abs heading hero-title">Advanced Oxidation Science</h1>
<p class="abs heading hero-sub">for Environmental Pollution Management</p>
<div class="abs scroll-btn">
  <svg width="36" height="36" viewBox="0 0 36 36"><path d="M11 15l7 7 7-7" fill="none" stroke="#1fb3bf" stroke-width="2.5"/></svg>
</div>

<!-- About -->
<section class="abs about">
  <h2 class="heading">About <span>Velqua</span></h2>
  <div class="copy">
    <p>Velqua Research develops advanced oxidation technologies and materials, which it licenses to Velqua Systems, China.</p>
    <p>Velqua Systems is engaged in the sales, service and support of environmental solutions for industry and government. With offices in Shanghai, Beijing, Shijiazhuang, and Chengdu, Velqua Systems is among the most advanced and rapidly growing companies offering solutions for air, water and fuel environmental compliance. Velqua Research Corporation supports these solutions with research and development.</p>
    <p>Velqua Research Corporation pursues business development opportunities in markets worldwide.</p>
  </div>
  <div class="abs photo-circle big" role="img" aria-label="Industrial silos and plant under a blue sky"></div>
  <div class="abs photo-circle small" role="img" aria-label="Red industrial filtration unit"></div>
</section>
<svg class="abs" style="left:0;top:650px" width="1200" height="40" viewBox="0 0 1200 40" preserveAspectRatio="none">
  <path d="M0 28 C300 0 500 6 700 20 C900 34 1050 14 1200 6 L1200 40 L0 40Z" fill="#4a90b6"/>
  <path d="M0 30 C300 2 500 8 700 22 C900 36 1050 16 1200 8" fill="none" stroke="#1fb3bf" stroke-width="8"/>
</svg>

<!-- Solutions -->
<h2 class="abs heading section-title" style="top:1384px">Solutions</h2>
<p class="abs section-sub" style="top:1450px">Environmental pollution control solutions employing nature's most reactive Free Radical</p>

<div class="abs solution" style="left:80px;top:1561px">
  <div class="icon-ring"><svg width="60" height="60" viewBox="0 0 60 60"><path d="M30 8 C20 24 16 30 16 38 a14 14 0 0 0 28 0 C44 30 40 24 30 8Z" fill="#1c86c6"/></svg></div>
  <h3>Water</h3>
  <p class="blurb">Lorem ipsum dolor sit amet, consectetur<br>adipiscing elit. Etiam vel odio interdum,<br>gravida tellus vel, ultrices odio.</p>
  <p class="read-more">Read More</p>
</div>
<div class="abs solution" style="left:439px;top:1561px">
  <div class="icon-ring"><svg width="64" height="64" viewBox="0 0 64 64"><circle cx="32" cy="32" r="6" fill="#1c86c6"/><path d="M32 26 C26 14 34 6 42 10 C46 16 40 24 32 26Z M37 35 C50 34 54 44 48 50 C40 50 36 44 37 35Z M27 35 C20 46 10 44 10 36 C14 28 22 28 27 35Z" fill="#1c86c6"/></svg></div>
  <h3>Air</h3>
  <p class="blurb">Lorem ipsum dolor sit amet, consectetur<br>adipiscing elit. Etiam vel odio interdum,<br>gravida tellus vel, ultrices odio.</p>
  <p class="read-more">Read More</p>
</div>
<div class="abs solution" style="left:797px;top:1561px">
  <div class="icon-ring"><svg width="60" height="60" viewBox="0 0 60 60"><path d="M30 6 C38 18 44 22 44 36 a14 14 0 0 1 -28 0 C16 26 22 22 24 14 C26 22 28 22 30 6Z" fill="#1c86c6"/><path d="M30 28 C34 34 36 36 36 41 a6 6 0 0 1 -12 0 C24 36 27 34 30 28Z" fill="#fff"/></svg></div>
  <h3>Fuel</h3>
  <p class="blurb">Lorem ipsum dolor sit amet, consectetur<br>adipiscing elit. Etiam vel odio interdum,<br>gravida tellus vel, ultrices odio.</p>
  <p class="read-more">Read More</p>
</div>

<!-- Advanced Oxidation -->
<section class="abs oxidation">
  <div class="photo" role="img" aria-label="Technician in protective gear handling chemical drums"></div>
  <h2 class="heading">Advanced <span>Oxidation</span></h2>
  <div class="copy">
    <p>Advanced Oxidation refers to a variety of techniques employing the Hydroxyl Radical, an energetic, highly reactive cousin of the water molecule:</p>
    <ul>
      <li>To add oxygen to inorganic molecules</li>
      <li>To remove hydrogen from organic molecules</li>
    </ul>
    <p>These transformations convert important industrial contaminants into reactive forms that can be captured or that disintegrate into harmless end products.</p>
  </div>
</section>

<!-- Products -->
<h2 class="abs heading section-title" style="top:2686px;color:var(--blue)">Our <span style="color:var(--teal)">Products</span></h2>

<div class="abs product" style="left:54px;top:2793px">
  <div class="disc" role="img" aria-label="Blue glass facade of a tower" style="background:linear-gradient(160deg,#9fd2ee,#2d7fb6)"></div>
  <h3>FLOXA</h3>
  <p class="kind">Flue Gas Advanced<br>Oxidation Catalytic Process</p>
  <hr>
  <p class="blurb">Lorem ipsum dolor sit amet,<br>consectetur adipiscing elit.</p>
  <p class="read-more">Read More</p>
</div>
<div class="abs product" style="left:330px;top:2793px">
  <div class="disc" role="img" aria-label="Solar panel array under a blue sky" style="background:linear-gradient(180deg,#3a78c4,#5e4a9a 60%,#2a3d7a)"></div>
  <h3>PHOTRA</h3>
  <p class="kind">Photo Electric Advanced<br>Oxidation Catalytic Process</p>
  <hr>
  <p class="blurb">Lorem ipsum dolor sit amet,<br>consectetur adipiscing elit.</p>
  <p class="read-more">Read More</p>
</div>
<div class="abs product" style="left:604px;top:2793px">
  <div class="disc" role="img" aria-label="Oil refinery at sunset" style="background:linear-gradient(180deg,#d9a47b,#8a5a4a 60%,#3b2e36)"></div>
  <h3>PETRAX</h3>
  <p class="kind">Petroleum Dehydrate Advanced<br>Oxidation Catalytic Process</p>
  <hr>
  <p class="blurb">Lorem ipsum dolor sit amet,<br>consectetur adipiscing elit.</p>
  <p class="read-more">Read More</p>
</div>
<div class="abs product" style="left:881px;top:2793px">
  <div class="disc" role="img" aria-label="Young plant growing with a butterfly" style="background:linear-gradient(180deg,#4aa6d6,#2d7fa8 60%,#2f5d44)"></div>
  <h3>VOLTRA</h3>
  <p class="kind">Volatile Organic Compounds<br>Advanced Oxidation Catalytic</p>
  <hr>
  <p class="blurb">Lorem ipsum dolor sit amet,<br>consectetur adipiscing elit.</p>
  <p class="read-more">Read More</p>
</div>

<!-- Contact -->
<div class="abs map" role="img" aria-label="Grey street map of the office location"></div>
<div class="abs card">
  <div class="brand"><span class="dot"></span>Velqua</div>
  <p class="intro">We welcome inquiries regarding the licensing, distribution, and purchase of our products, systems, and technologies.</p>
  <div class="contact-row">
    <span class="ring"><svg width="20" height="20" viewBox="0 0 20 20"><path d="M5 2l3 4-2 2c1 2 3 4 5 5l2-2 4 3-2 3C9 17 3 11 2 5Z" fill="#1fb3bf"/></svg></span>
    <div><b>+1-555-010-4420</b><small>Contact Time : 8am - 9pm</small></div>
  </div>
  <div class="contact-row">
    <span class="ring"><svg width="20" height="20" viewBox="0 0 20 20"><rect x="2" y="4" width="16" height="12" fill="none" stroke="#1fb3bf" stroke-width="2"/><path d="M2 4l8 7 8-7" fill="none" stroke="#1fb3bf" stroke-width="2"/></svg></span>
    <div><b style="font-size:16px">info@velquaresearch.example</b><small>Get your doubts cleared</small></div>
  </div>
</div>

<!-- Partners -->
<section class="abs partners">
  <div class="abs partner" style="left:92px;top:40px">
    <div class="name">Velqua Systems</div>
    <p class="cap">Sales Partner<br>in China</p>
  </div>
  <div class="abs partner" style="left:346px;top:40px">
    <div class="name">Norvane</div>
    <p class="cap">Our construction<br>partner in China</p>
  </div>
  <div class="abs partner" style="left:608px;top:40px">
    <div class="badge"></div>
    <p class="cap">Technology partner<br>in China</p>
  </div>
  <div class="abs partner" style="left:868px;top:40px">
    <div class="badge"></div>
    <p class="cap">Technology partner<br>in China</p>
  </div>
</section>

<!-- Footer -->
<footer class="abs footer">
  <svg class="abs" style="left:0;top:-10px" width="1200" height="40" viewBox="0 0 1200 40" preserveAspectRatio="none">
    <path d="M0 10 C300 30 600 0 900 14 C1050 22 1150 12 1200 8 L1200 40 L0 40Z" fill="#1fb3bf"/>
    <path d="M0 22 C300 40 600 14 900 26 C1050 32 1150 24 1200 20 L1200 40 L0 40Z" fill="#1a7bc1"/>
  </svg>
  <div class="brand"><span class="dot"></span>Velqua</div>
  <div class="rule" style="left:270px;width:220px"></div>
  <div class="social" style="left:496px"></div>
  <div class="social" style="left:546px"></div>
  <div class="social" style="left:596px"></div>
  <div class="rule" style="left:650px;width:200px"></div>
  <p class="copy">© 2016. Copyrights. All Rights Reserved</p>
</footer>

</body>
</html>
```